Business card for my new company (Accounting firm)

I need a business card for my new business Brightwell Advisory and Ledger SA. Our services are accounting, tax, audit and financial management. Our customers are small companies, start-ups and new companies. The final design has to show financial security, trust and growth. Please find our logo attached to the business card. Text for the business card: Brightwell Advisory and Ledger SA Tomas Varenholt Director and Founder Certified Accountant Tel. 022 418 57 34 tv@clairevalconseil.ch www.clairevalconseil.ch Rue des Vergières 27 1201 Geneva
Target Market(s)
Our customers are small companies, start-ups and new companies.
Industry/Entity Type
Finance And Accounting
Contact Information for Business Card
Claireval Conseil et Comptes SA
Tomas Varenholt
Directeur et Fondateur
Expert-comptable diplômé
Tél. 022 418 57 34
tv@clairevalconseil.ch
www.clairevalconseil.ch
Rue des Vergières 27
1201 Genève

```html
<!DOCTYPE html>
<html lang="fr">
<head>
<meta charset="utf-8">
<title>Claireval Conseil et Comptes SA – Carte de visite</title>
<link rel="stylesheet" href="https://fonts.googleapis.com/css2?family=Roboto:wght@400;500;700&display=swap">
<style>
  :root {
    --backdrop: #e4e5e7;
    --card: #fafafa;
    --blue-light: #2a9fd8;
    --blue-mid: #1c7fbf;
    --blue-deep: #17588f;
    --charcoal: #3a3b3d;
    --text-grey: #4a4c50;
  }
  * { box-sizing: border-box; margin: 0; padding: 0; }
  html, body { width: 1200px; height: 726px; overflow: hidden; }
  body {
    background: var(--backdrop);
    font-family: "Roboto", Arial, sans-serif;
    display: flex;
    align-items: center;
    justify-content: center;
    gap: 50px;
  }
  .card {
    position: relative;
    width: 540px;
    height: 318px;
    background: var(--card);
    box-shadow: 0 6px 18px rgba(0,0,0,0.12);
    overflow: hidden;
  }

  /* wordmark */
  .wordmark {
    display: flex;
    align-items: center;
    gap: 10px;
    color: var(--blue-deep);
    font-weight: 700;
  }
  .wordmark__square {
    width: 22px; height: 22px;
    background: var(--blue-light);
    flex: none;
  }
  .wordmark__name { line-height: 1.1; letter-spacing: 0.02em; }

  /* front */
  .card--front .wordmark {
    position: absolute;
    left: 50%; top: 118px;
    transform: translateX(-50%);
    font-size: 24px;
    white-space: nowrap;
  }
  .front-band {
    position: absolute;
    left: 0; right: 0; bottom: 40px;
    height: 9px;
    background: linear-gradient(to bottom, var(--blue-light) 0 55%, var(--blue-mid) 55% 100%);
  }

  /* back */
  .card--back .wordmark {
    position: absolute;
    right: 28px; top: 40px;
    font-size: 16px;
    width: 190px;
  }
  .holder { position: absolute; left: 32px; top: 92px; }
  .holder__name { color: var(--blue-deep); font-weight: 700; font-size: 22px; }
  .holder__role { color: var(--text-grey); font-size: 13px; line-height: 1.3; margin-top: 6px; }

  .contacts {
    position: absolute; left: 32px; bottom: 40px;
    list-style: none;
    color: var(--text-grey);
    font-size: 14px;
  }
  .contacts li { display: flex; align-items: center; gap: 12px; line-height: 21px; }
  .contacts svg { width: 13px; height: 13px; fill: var(--blue-deep); flex: none; }

  .address-tab {
    position: absolute; right: 0; bottom: 18px;
    width: 262px; height: 50px;
    background: linear-gradient(to right, var(--blue-deep), var(--blue-light));
    border-top-left-radius: 18px;
    color: #fff;
    font-size: 14px;
    display: flex; align-items: center; justify-content: center;
  }
  .base-strip {
    position: absolute; left: 0; right: 0; bottom: 0;
    height: 18px;
    background: var(--charcoal);
  }
</style>
</head>
<body>

<section class="card card--front" aria-label="Recto">
  <div class="wordmark">
    <span class="wordmark__square"></span>
    <span class="wordmark__name">Claireval Conseil et Comptes</span>
  </div>
  <div class="front-band"></div>
</section>

<section class="card card--back" aria-label="Verso">
  <div class="wordmark">
    <span class="wordmark__square"></span>
    <span class="wordmark__name">Claireval Conseil et Comptes</span>
  </div>

  <div class="holder">
    <h1 class="holder__name">Tomas Varenholt</h1>
    <p class="holder__role">Directeur et Fondateur<br>Expert-comptable diplômé</p>
  </div>

  <ul class="contacts">
    <li>
      <svg viewBox="0 0 24 24" aria-hidden="true"><path d="M6.6 10.8a15.2 15.2 0 0 0 6.6 6.6l2.2-2.2a1 1 0 0 1 1-.25 11.4 11.4 0 0 0 3.6.57 1 1 0 0 1 1 1V20a1 1 0 0 1-1 1A17 17 0 0 1 3 4a1 1 0 0 1 1-1h3.5a1 1 0 0 1 1 1c0 1.25.2 2.45.57 3.57a1 1 0 0 1-.25 1z"/></svg>
      022 418 57 34
    </li>
    <li>
      <svg viewBox="0 0 24 24" aria-hidden="true"><path d="M2 5h20v14H2zm2 2v.5l8 5 8-5V7zm0 2.8V17h16V9.8l-8 5z"/></svg>
      tv@clairevalconseil.ch
    </li>
    <li>
      <svg viewBox="0 0 24 24" aria-hidden="true"><path d="M12 2a10 10 0 1 0 0 20 10 10 0 0 0 0-20zm6.9 6h-3a15 15 0 0 0-1.3-3.9A8 8 0 0 1 18.9 8zM12 4c.8 1.2 1.5 2.5 1.9 4h-3.8c.4-1.5 1.1-2.8 1.9-4zM4.3 14a8 8 0 0 1 0-4h3.4a16 16 0 0 0 0 4zm.8 2h3a15 15 0 0 0 1.3 3.9A8 8 0 0 1 5.1 16zm3-8h-3a8 8 0 0 1 4.3-3.9A15 15 0 0 0 8.1 8zM12 20c-.8-1.2-1.5-2.5-1.9-4h3.8c-.4 1.5-1.1 2.8-1.9 4zm2.3-6H9.7a14 14 0 0 1 0-4h4.6a14 14 0 0 1 0 4zm.3 5.9a15 15 0 0 0 1.3-3.9h3a8 8 0 0 1-4.3 3.9zm1.7-5.9a16 16 0 0 0 0-4h3.4a8 8 0 0 1 0 4z"/></svg>
      www.clairevalconseil.ch
    </li>
  </ul>

  <div class="address-tab">Rue des Vergières 27 1201 Genève</div>
  <div class="base-strip"></div>
</section>

</body>
</html>
```